Standardization and redesign of graphics for a non-fiction book

For a book project, 11 graphics need to be visually unified so that all the graphics in the book are in the same style. The graphics must be created from scratch. Just new colors aren't enough. Some of the existing graphics are by other authors who own the copyright. Accordingly, the new graphics must be truly new. This is especially true for the "2 S-curves" graphic.

Target Market(s)

Manager Furniture Industry

Industry/Entity Type

Möbel

Colors
0054AA
0677BA
7BADD7
CADEEF
E8F1F8

```html
<!DOCTYPE html>
<html lang="de">
<head>
<meta charset="utf-8">
<title>Geschäftsmodell – Zielkunde</title>
<link href="https://fonts.googleapis.com/css2?family=Poppins:wght@400;700&display=swap" rel="stylesheet">
<style>
  :root {
    --title-blue: #0054AA;
    --frame-blue: #2AA6E6;
    --ring-blue: #2BA9EC;
    --text-dark: #111111;
    --hub-top: #2AEDF0;
    --hub-bottom: #14B2D6;
    --paper: #FFFFFF;
  }
  html, body {
    margin: 0;
    padding: 0;
    width: 1200px;
    height: 1200px;
    overflow: hidden;
    background: var(--paper);
  }
  .diagram {
    position: relative;
    width: 1200px;
    height: 1200px;
    font-family: "Poppins", sans-serif;
  }
  .ring {
    position: absolute;
    left: 0;
    top: 0;
  }
  .hub {
    position: absolute;
    left: 481px;
    top: 481px;
    width: 241px;
    height: 241px;
    border-radius: 50%;
    background: linear-gradient(160deg, var(--hub-top) 0%, var(--hub-bottom) 100%);
    display: flex;
    align-items: center;
    justify-content: center;
    color: var(--paper);
    font-weight: 700;
    font-size: 32px;
    letter-spacing: 0.2px;
  }
  .element {
    position: absolute;
    box-sizing: border-box;
    background: var(--paper);
    border: 2px solid var(--frame-blue);
    border-radius: 40px;
    padding: 22px 18px 0;
    text-align: center;
  }
  .element-title {
    margin: 0 0 14px;
    color: var(--title-blue);
    font-weight: 700;
    font-size: 17.6px;
    line-height: 1.3;
  }
  .element-text {
    margin: 0;
    color: var(--text-dark);
    font-size: 12.6px;
    line-height: 17.6px;
  }
  .element-text + .element-text { margin-top: 6px; }

  .leistungskonzept   { left: 435px; top: 223px; width: 333px; height: 194px; }
  .kanaele            { left: 773px; top: 417px; width: 296px; height: 162px; }
  .wertschoepfung     { left: 753px; top: 647px; width: 332px; height: 194px; }
  .wertverteilung     { left: 455px; top: 826px; width: 292px; height: 150px; }
  .ertragsmodell      { left: 146px; top: 654px; width: 313px; height: 161px; }
  .entwicklung        { left: 116px; top: 407px; width: 332px; height: 194px; }
  .entwicklung .element-title { padding-left: 50px; }
</style>
</head>
<body>
<main class="diagram">
  <svg class="ring" width="1200" height="1200" viewBox="0 0 1200 1200" aria-hidden="true">
    <ellipse cx="601" cy="601" rx="298" ry="312" fill="none" stroke="var(--ring-blue)" stroke-width="11"/>
  </svg>

  <div class="hub">Zielkunde</div>

  <section class="element leistungskonzept">
    <h2 class="element-title">Leistungskonzept</h2>
    <p class="element-text">Angebotspalette:</p>
    <p class="element-text">Wohnungseinrichtungsgegenstände und damit verbundenen Dienstleistungen wie Beratung, Lieferung, Entsorgung, Reparatur, Ersatzteile, ...</p>
  </section>

  <section class="element kanaele">
    <h2 class="element-title">Kanäle</h2>
    <p class="element-text">Kommunikations- und<br>Verkaufskanäle (Single-, Multiple-<br>und Omni-Channel)POS-Konzept</p>
  </section>

  <section class="element wertschoepfung">
    <h2 class="element-title">Wertschöpfungskonzept</h2>
    <p class="element-text">vertikale Integration vs reiner Handel, Einkaufsstrategie (Global- oder Local-Sourcing, Lagerhaltung, Einzelstückfertigung, ...)Innenarchitektur, komplexe Einrichtungsberatung, Farb- und Stylingkonzepte, ...</p>
  </section>

  <section class="element wertverteilung">
    <h2 class="element-title">Wertverteilung</h2>
    <p class="element-text">Shareholder-Konzept, Einbezug des Managements und der Mitarbeiter, Öffentlichkeitsinteresse</p>
  </section>

  <section class="element ertragsmodell">
    <h2 class="element-title">Ertragsmodell</h2>
    <p class="element-text">margengetriebenes Modell<br>(Verkaufspreise), Miete,<br>Dienstleistungsgebühren (Living as a<br>Service, Logistik, Reparatur)</p>
  </section>

  <section class="element entwicklung">
    <h2 class="element-title">Entwicklungskonzept</h2>
    <p class="element-text">z.B. Open Innovation im Rahmen eines<br>2-S-Kurven-ModellsService- &amp;<br>ProduktentwicklungDigitalstrategie,<br>Nachhaltigkeitsstrategie</p>
  </section>
</main>
</body>
</html>
```